Stationery for use with Ninefold Ridge reports

I would like to get a stationery design that my firm -- Ninefold Ridge Advisory -- will use as a format for reports that we send our clients. I am specifically looking for a design for use on a piece of paper or letterhead -- not business cards or envelopes.

We are an Africa based US risk intelligence and strategy firm that works with multinational corporations operating in West Africa. Our initial thinking is that we would like a color scheme consistent with our existing logo -- however we are open to other color schemes.

Also, we would like to see at least two separate versions: one with our company name and logo, the other without name and logo.

We also would like font recommendations for the stationary design.

The final design should communicate discreet professionalism and a modern approach, but it should not overshadow the words and information printed on the stationery.

Target Market(s)

Multinational corporations that currently use our products.

Font styles to use
Serif
Sans Serif

Requirements
Must have
• Sense of discreet professionalism that will not overshadow the content we put onto the stationery format.
• We would like to see designs with and without our company name/logo.
• Please suggest fonts that would work with the stationery.
Nice to have
• Ideally colors consistent with out existing logo, though we are open to and even encourage other ideas.
Should not have
• No need for business cards or envelopes.

```html
<!DOCTYPE html>
<html lang="en">
<head>
<meta charset="utf-8">
<title>Ninefold Ridge Advisory — Letterhead</title>
<link rel="stylesheet" href="https://fonts.googleapis.com/css2?family=Roboto:wght@400;700&display=swap">
<style>
  :root {
    --backdrop: #cfebf3;
    --paper: #ffffff;
    --navy: #1f3a4a;
    --gold: #e2a93b;
    --rule-grey: #8a96a0;
    --ink: #555a5e;
    --ink-soft: #6b7075;
    --sign-tone: #e6e8ea;
  }
  * { box-sizing: border-box; margin: 0; padding: 0; }
  html, body { width: 1200px; height: 1200px; overflow: hidden; }
  body {
    background: var(--backdrop);
    font-family: "Roboto", Arial, sans-serif;
    position: relative;
  }
  .sheet {
    position: absolute;
    left: 243px; top: 95px;
    width: 715px; height: 1010px;
    background: var(--paper);
  }
  .contact {
    position: absolute;
    left: 35px; top: 65px;
    font-size: 12px;
    line-height: 15px;
    color: var(--ink);
    list-style: none;
  }
  .contact li { display: flex; align-items: center; gap: 6px; }
  .contact svg { width: 9px; height: 9px; fill: var(--gold); }
  .contact .web-name { color: var(--gold); }
  .address {
    position: absolute;
    right: 36px; top: 80px;
    text-align: right;
    font-size: 12px;
    line-height: 15px;
    color: var(--ink);
  }
  .brand-mark {
    position: absolute;
    left: 338px; top: 44px;
    width: 40px; height: 40px;
    border-radius: 50%;
    background: var(--gold);
  }
  .rule { position: absolute; height: 0; }
  .rule-gold { top: 128px; height: 3px; background: var(--gold); }
  .rule-grey { top: 142px; height: 1px; background: var(--rule-grey); }
  .rule-gold.left { left: 0; width: 268px; }
  .rule-gold.right { right: 0; width: 268px; }
  .rule-grey.left { left: 0; width: 268px; }
  .rule-grey.right { right: 0; width: 268px; }
  .brand-name {
    position: absolute;
    left: 268px; width: 179px; top: 112px;
    text-align: center;
    font-weight: 700;
    font-size: 13.5px;
    line-height: 36px;
    letter-spacing: 0.3px;
    color: var(--navy);
    white-space: nowrap;
  }
  .letter {
    position: absolute;
    left: 71px; top: 0;
    width: 590px;
    font-size: 12.5px;
    color: var(--ink);
  }
  .letter-date { position: absolute; top: 301px; line-height: 18px; white-space: nowrap; }
  .letter-body { position: absolute; top: 358px; }
  .letter-body p { line-height: 26px; white-space: nowrap; margin-bottom: 3px; }
  .letter-body p.gap { margin-bottom: 6px; }
  .signature-area {
    position: absolute;
    left: 497px; top: 700px;
    width: 148px; height: 48px;
    background: linear-gradient(90deg, var(--sign-tone), #f4f5f6);
  }
  .signatory {
    position: absolute;
    left: 502px; top: 746px;
    font-size: 12.5px;
    line-height: 14px;
    color: var(--ink);
  }
</style>
</head>
<body>
  <main class="sheet">
    <ul class="contact">
      <li><svg viewBox="0 0 10 10"><path d="M2 0.5 L4 2.8 L3 4 Q4 6 6 7 L7.2 6 L9.5 8 L8 9.7 Q4 9.5 0.3 2 Z"/></svg>555-014-2100</li>
      <li><svg viewBox="0 0 10 10"><path d="M0 2 H10 V8 H0 Z M0.8 2.6 L5 5.6 L9.2 2.6" /></svg>hello@ninefoldridge.com</li>
      <li><svg viewBox="0 0 10 10"><circle cx="5" cy="5" r="4.5"/></svg><span>www.<span class="web-name">ninefoldridge</span>.com</span></li>
    </ul>

    <div class="brand-mark"></div>
    <div class="rule rule-gold left"></div>
    <div class="rule rule-gold right"></div>
    <div class="rule rule-grey left"></div>
    <div class="rule rule-grey right"></div>
    <div class="brand-name">Ninefold Ridge Advisory</div>

    <address class="address" style="font-style:normal">Your address, city<br>state, ZIP 0000</address>

    <article class="letter">
      <p class="letter-date">Date, 10 September, 2020</p>
      <div class="letter-body">
        <p class="gap">This is a sample letter that has been placed to demonstrate typing remat (Your Company). letterhead<br>design. When positioned properly, it will serve to work in harmony with all other elements letterhead.<br>This letterhead design is meant to project an image</p>
        <p class="gap">This letterhead design is meant project an image of professionalism reliability. By using simple aligen<br>we have created a very spacious feeling. The simplicity suggest&nbsp; rengththe spaciousnes contributes h<br>aesthetics the layout. These basic qualities along with the (Your Company)</p>
        <p class="gap">look and helps reinforce the (Your Company) brand. letterhead design is meant to project an image p<br>design. When positioned properly, it will serve to work in harmony all the other elements letterhead.<br>sionalism and reliability.</p>
        <p>This letterhead design is based on the (Form of your logo) form (Your Company) logo. Each stationery<br>we have created a very spacious feeling. The simplicity suggests strength the spaciousnes contribute<br>part of the (Form of your logo).</p>
      </div>
    </article>

    <div class="signature-area" role="img" aria-label="Handwritten signature of Dana Whitlow"></div>
    <p class="signatory">Dana Whitlow<br>Manager</p>
  </main>
</body>
</html>
```